The Linen Loft Co

We need a business card design for our wardrobe company.
Please visit our website www.gentlelinenlofts.com to get an idea of who we are.

```html
<!DOCTYPE html>
<html lang="en">
<head>
<meta charset="utf-8">
<title>The Linen Loft Co — Business Card</title>
<link rel="stylesheet" href="https://fonts.googleapis.com/css2?family=Roboto:wght@400;500;700&display=swap">
<style>
  :root {
    --backdrop: #2a2622;
    --card: #ffffff;
    --ink: #111111;
    --ink-soft: #555555;
    --ink-muted: #a8a8a8;
    --rule: #c9c9c9;
  }
  * { margin: 0; padding: 0; box-sizing: border-box; }
  html, body {
    width: 1200px; height: 801px; overflow: hidden;
    background: var(--backdrop);
    font-family: "Roboto", Arial, sans-serif;
  }
  .card {
    position: absolute; left: 125px; top: 129px;
    width: 950px; height: 543px;
    background: var(--card);
    color: var(--ink);
  }
  .brand {
    position: absolute; left: 560px; top: 150px;
    display: flex; align-items: center; gap: 16px;
  }
  .brand-mark { width: 22px; height: 22px; background: var(--ink); }
  .brand-text { font-size: 22px; font-weight: 500; line-height: 1.3; }
  .brand-name { text-transform: uppercase; letter-spacing: 0.2px; }
  .brand-tagline { font-weight: 500; }
  .person { position: absolute; left: 64px; top: 190px; }
  .person-name { font-size: 38px; font-weight: 700; letter-spacing: -0.3px; }
  .person-role { font-size: 22px; color: var(--ink-muted); margin-top: 2px; }
  .person-rule {
    width: 250px; height: 1px; background: var(--rule); margin-top: 10px;
  }
  .contacts {
    position: absolute; left: 64px; top: 305px;
    list-style: none; font-size: 22px; color: var(--ink-soft);
  }
  .contact { display: flex; align-items: center; gap: 14px; height: 30px; }
  .contact svg { width: 16px; height: 16px; fill: var(--ink); flex: none; }
  .divider {
    position: absolute; left: 64px; top: 415px;
    width: 790px; height: 1px; background: var(--rule);
  }
  .address {
    position: absolute; right: 96px; top: 440px;
    text-align: right; font-size: 22px; line-height: 1.35; color: var(--ink-soft);
    font-style: normal;
  }
</style>
</head>
<body>
  <main class="card">
    <div class="brand">
      <span class="brand-mark"></span>
      <div class="brand-text">
        <div class="brand-name">The Linen Loft Co</div>
        <div class="brand-tagline">Crafted for Calm Spaces</div>
      </div>
    </div>

    <div class="person">
      <h1 class="person-name">Daniel Hart</h1>
      <p class="person-role">President</p>
      <div class="person-rule"></div>
    </div>

    <ul class="contacts">
      <li class="contact">
        <svg viewBox="0 0 16 16" aria-hidden="true"><path d="M3.5 1 6 1.5 7 5 5.3 6.3c.8 1.8 2.3 3.3 4.2 4.2L10.8 8.8 14.5 9.8 15 12.3c-.2 1.5-1.4 2.6-3 2.6C6 14.5 1.4 10 1.1 4 1 2.5 2 1.3 3.5 1Z"/></svg>
        020 7946 0318
      </li>
      <li class="contact">
        <svg viewBox="0 0 16 16" aria-hidden="true"><path d="M1 3h14v10H1Z" fill="none" stroke="#111" stroke-width="1.6"/><path d="M1 3.5 8 9l7-5.5" fill="none" stroke="#111" stroke-width="1.6"/></svg>
        info@gentlelinenlofts.com
      </li>
      <li class="contact">
        <svg viewBox="0 0 16 16" aria-hidden="true"><circle cx="8" cy="8" r="7"/></svg>
        www.gentlelinenlofts.com
      </li>
    </ul>

    <div class="divider"></div>

    <address class="address">
      Harbour House, 42 Mill Lane<br>
      London N4 7QP
    </address>
  </main>
</body>
</html>
```